Business Cards Design for the electrical wholesaler: clean bold dynamic :)

We need a business card design that would follow our latest brand guidelines. As an electrical wholesaler we want to bring a fresh look and feel into the industry. The design should be clean bold and dynamic. It should come alive with the renewed energy of our green colour. Our grey colour should keep things balanced and complement the notion of maturity and responsibility. We employ Lato as a corporate font however are not bound by this font and we’re open to interpretation here.

Target Market(s)

Electrical contractors

Industry/Entity Type

Business

Contact Information for Business Card

Logo
Name & Surname: Halyna Dorosh
Job Title: Director of Marketing
Email: halya.dorosh@quillmail.example
Cell phone: XXX.XXX.XXXX
Address: 20517 - 87 Ave. Edmonton, AB, Canada. T6K 4N8
Business Phone: 780.555.0184
Website: www.brovix.example

Font styles to use
Other font styles liked:
• Lato

Requirements
Must have
• Logo & website
Nice to have
• Brand elements - some of them you may find in the attached Brand Guidelines (e.g. three lines on the background signifying "W")

```html
<!DOCTYPE html>
<html lang="en">
<head>
<meta charset="utf-8">
<title>Brovix business cards</title>
<link href="https://fonts.googleapis.com/css2?family=Work+Sans:wght@400;500&display=swap" rel="stylesheet">
<style>
  :root {
    --green: #8cc63f;
    --grey: #58595b;
    --grey-dark: #4d4e50;
    --white: #ffffff;
    --backdrop: #1f1f1f;
  }
  html, body {
    margin: 0;
    width: 1200px;
    height: 897px;
    overflow: hidden;
    background: var(--backdrop);
    font-family: "Work Sans", sans-serif;
  }
  .card {
    position: absolute;
    left: 303px;
    width: 595px;
    height: 338px;
    border-radius: 16px;
    overflow: hidden;
    box-shadow: 0 10px 24px rgba(0,0,0,.55);
  }
  .card-front { top: 92px; background: var(--white); }
  .card-back { top: 469px; background: var(--grey); }
  .wave { position: absolute; inset: 0; width: 100%; height: 100%; }
  .brand {
    position: absolute;
    display: flex;
    align-items: center;
    gap: 12px;
    font-weight: 500;
    line-height: 1;
    letter-spacing: -1px;
  }
  .brand-mark { width: 40px; height: 40px; background: var(--green); border-radius: 4px; }
  .card-front .brand { left: 26px; top: 38px; font-size: 56px; color: var(--grey); }
  .card-back .brand { left: 0; right: 0; top: 132px; justify-content: center; font-size: 62px; color: var(--white); }
  .card-back .brand-mark { width: 46px; height: 46px; }
  .person { position: absolute; right: 33px; top: 34px; text-align: right; }
  .person-name { color: var(--green); font-size: 24px; font-weight: 500; line-height: 1.1; }
  .person-title { color: var(--grey); font-size: 15px; letter-spacing: .5px; margin-top: 3px; }
  .contacts {
    position: absolute; right: 33px; top: 204px;
    color: var(--white); font-size: 14.5px; letter-spacing: .5px; text-align: right;
  }
  .contact-line { display: flex; justify-content: flex-end; align-items: center; gap: 8px; height: 19px; }
  .contact-line svg { width: 10px; height: 10px; }
  .address { margin-top: 11px; line-height: 20px; padding-right: 0; }
  .accent { color: var(--green); }
  .back-web {
    position: absolute; left: 0; right: 0; top: 296px;
    text-align: center; color: var(--white); font-size: 14.5px; letter-spacing: .5px;
  }
</style>
</head>
<body>
  <section class="card card-front">
    <svg class="wave" viewBox="0 0 595 338" aria-hidden="true">
      <path d="M0,262 C170,330 320,240 430,185 C510,148 565,158 595,168 L595,338 L0,338 Z" fill="var(--grey)"/>
      <path d="M40,300 C200,320 330,230 430,180 C500,146 560,150 575,148 C540,134 470,136 400,175 C300,232 190,305 40,300 Z" fill="var(--grey)"/>
      <path d="M40,300 C200,316 330,226 430,177 C497,144 555,146 575,148" fill="none" stroke="var(--white)" stroke-width="4"/>
      <path d="M0,250 C100,285 200,240 295,192 C220,240 110,292 0,262 Z" fill="var(--green)"/>
    </svg>
    <div class="brand"><span class="brand-mark"></span>brovix</div>
    <div class="person">
      <div class="person-name">Halyna Dorosh</div>
      <div class="person-title">Founder</div>
    </div>
    <div class="contacts">
      <div class="contact-line">780.555.0184
        <svg viewBox="0 0 10 10"><path d="M2,1 L4,1 L4.5,3 L3.3,4 C4,5.5 4.8,6.4 6,7 L7,5.7 L9,6.3 L9,8.5 C5,8.7 1.5,5 2,1 Z" fill="var(--green)"/></svg></div>
      <div class="contact-line">hello@brovix.example
        <svg viewBox="0 0 10 10"><rect x="1" y="2.5" width="8" height="5.5" fill="none" stroke="var(--green)" stroke-width="1"/><path d="M1,2.5 L5,5.5 L9,2.5" fill="none" stroke="var(--green)" stroke-width="1"/></svg></div>
      <div class="contact-line">www.<span class="accent">brovix</span>.example
        <svg viewBox="0 0 10 10"><circle cx="5" cy="5" r="4" fill="none" stroke="var(--green)" stroke-width="1"/><path d="M1,5 H9 M5,1 C3,3.5 3,6.5 5,9 M5,1 C7,3.5 7,6.5 5,9" fill="none" stroke="var(--green)" stroke-width=".8"/></svg></div>
      <div class="address">20517 87ave<br>T6K4N8 Edmonton, Alberta</div>
    </div>
  </section>

  <section class="card card-back">
    <div class="brand"><span class="brand-mark"></span>brovix</div>
    <div class="back-web">www.<span class="accent">brovix</span>.example</div>
  </section>
</body>
</html>
```